Business Card Design Project

I require a business card with the following information on them for various different people;
name
m:
f:
e:
I have a logo already and will attached that. We are in the construction industry. I require something clean and simple but eye catching at the same time. You can use another colour with our logo if you like and you can style the logo as well if you wish. I am open.
Also it needs to be front and back design.
Industry/Entity Type
Construction
Requirements
Must have
- Logo, name, mobile, fax and email address.
Front and back design

```html
<!DOCTYPE html>
<html lang="en">
<head>
<meta charset="utf-8">
<title>Harbor Crest Builders – Business Card</title>
<link href="https://fonts.googleapis.com/css2?family=Questrial&family=Libre+Baskerville&family=Arimo&display=swap" rel="stylesheet">
<style>
  :root {
    --backdrop: #1c1c1c;
    --card-top: #3d1618;
    --card-bottom: #240b0d;
    --band-black: #050505;
    --brand-green: #7cc242;
    --green-light: #9ad84f;
    --green-dark: #3f7a1c;
    --text-white: #f2f2f2;
  }
  * { margin: 0; padding: 0; box-sizing: border-box; }
  html, body {
    width: 1200px;
    height: 900px;
    overflow: hidden;
    background: var(--backdrop);
  }
  .sheet {
    width: 1200px;
    height: 900px;
    display: flex;
    flex-direction: column;
    align-items: center;
    justify-content: center;
    gap: 40px;
  }
  .card {
    position: relative;
    width: 700px;
    height: 400px;
    background: radial-gradient(ellipse at 50% 20%, var(--card-top), var(--card-bottom) 80%);
    box-shadow: 0 10px 30px rgba(0,0,0,0.6);
    overflow: hidden;
  }
  .brand {
    position: absolute;
    left: 0;
    right: 0;
    display: flex;
    align-items: center;
    justify-content: center;
    gap: 14px;
    font-family: "Questrial", sans-serif;
    color: var(--brand-green);
    line-height: 1;
  }
  .brand-mark {
    background: var(--brand-green);
  }
  .brand-name {
    text-align: center;
  }
  .card-front .brand { top: 60px; font-size: 40px; }
  .card-front .brand-mark { width: 34px; height: 34px; }
  .card-back .brand { top: 145px; font-size: 58px; }
  .card-back .brand-mark { width: 48px; height: 48px; }

  .holder-name {
    position: absolute;
    left: 40px;
    top: 205px;
    font-family: "Libre Baskerville", serif;
    font-size: 22px;
    color: var(--brand-green);
  }
  .rule {
    position: absolute;
    left: 0;
    right: 0;
    top: 238px;
    height: 3px;
    background: var(--brand-green);
  }
  .contact-band {
    position: absolute;
    left: 0;
    right: 0;
    top: 241px;
    height: 110px;
    background: var(--band-black);
    display: flex;
    flex-direction: column;
    align-items: center;
    justify-content: center;
    gap: 8px;
    font-family: "Arimo", sans-serif;
    font-size: 18px;
    color: var(--text-white);
  }
  .contact-label { color: var(--brand-green); }
  .contact-row span + span.contact-label { margin-left: 18px; }
  .green-strip {
    position: absolute;
    left: 0;
    right: 0;
    top: 351px;
    bottom: 0;
    background: linear-gradient(to bottom, var(--green-light), var(--brand-green) 50%, var(--green-dark));
  }
</style>
</head>
<body>
<main class="sheet">
  <section class="card card-front">
    <div class="brand">
      <span class="brand-mark"></span>
      <span class="brand-name">Harbor Crest<br>Builders</span>
    </div>
    <p class="holder-name">Your Name</p>
    <div class="rule"></div>
    <div class="contact-band">
      <p class="contact-row"><span class="contact-label">Mobile</span> <span>: xxxxxxxxxx</span><span class="contact-label">Fax</span> <span>: xxx xxx xxx</span></p>
      <p class="contact-row"><span class="contact-label">E-mail</span> <span>: name@domain.com</span></p>
    </div>
    <div class="green-strip"></div>
  </section>

  <section class="card card-back">
    <div class="brand">
      <span class="brand-mark"></span>
      <span class="brand-name">Harbor Crest<br>Builders</span>
    </div>
  </section>
</main>
</body>
</html>
```